Brivane Management

We need a web design for a new consulting company, with clients all over the world. The company provides management consulting to the travel industry.

Logo files are attached.

Website must look very corporate and be responsive in design.

Management Consulting

```html
<!DOCTYPE html>
<html lang="en">
<head>
<meta charset="utf-8">
<title>Brivane Strategy Management, Inc.</title>
<link href="https://fonts.googleapis.com/css2?family=Lato:ital,wght@0,400;0,700;1,700;1,900&family=Open+Sans:wght@400;600&display=swap" rel="stylesheet">
<style>
:root{
  --page-dark:#1d1a18;
  --page-mid:#2e2926;
  --brand-blue:#0c6fc6;
  --brand-blue-dark:#0a5aa6;
  --brand-green:#6cbb23;
  --ink:#1f2a36;
  --text:#3d3d3d;
  --muted:#8b8b8b;
  --grey-band:#e4e4e4;
  --circle-grey:#6f6f6f;
  --white:#ffffff;
}
*{margin:0;padding:0;box-sizing:border-box}
html,body{width:1200px;height:1002px;overflow:hidden}
body{position:relative;background:radial-gradient(ellipse at 50% 40%,var(--page-mid),var(--page-dark) 70%);font-family:'Lato',sans-serif;color:var(--text)}
.side-art{position:absolute;width:140px;height:300px;background:radial-gradient(circle at 30% 50%,#6b7f95 0%,#3b3a3e 45%,transparent 75%);opacity:.7}
.side-art--left{left:0;top:0}
.side-art--right{right:0;top:600px;background:radial-gradient(circle at 70% 50%,#6b7f95 0%,#3b3a3e 45%,transparent 75%)}
.hero{position:absolute;left:139px;top:0;width:923px;height:476px;background:linear-gradient(100deg,#cfdde5 0%,#a9bfcc 45%,#4a5560 68%,#2a2f36 85%,#8fa7b6 100%)}
.phone-top{position:absolute;left:190px;top:14px;display:flex;align-items:center;gap:8px;font-size:19px;font-weight:700;color:#2a2a2a}
.icon-dot{width:30px;height:30px;border-radius:50%;background:var(--brand-green);display:flex;align-items:center;justify-content:center}
.header-bar{position:absolute;left:150px;top:54px;width:966px;height:67px}
.brand{position:absolute;left:175px;top:66px;display:flex;align-items:center;gap:12px}
.brand-mark{width:44px;height:44px;border-radius:50%;background:var(--brand-blue)}
.brand-name{font-size:30px;font-weight:700;color:var(--ink);line-height:1}
.brand-sub{font-size:11px;font-weight:700;color:var(--ink);letter-spacing:1.5px;margin-top:3px}
.nav{position:absolute;left:544px;top:54px;height:67px;display:flex;font-size:19px}
.nav a{color:#1f2a36;text-decoration:none;display:flex;align-items:center;padding:0 17px}
.nav a.is-active{background:var(--brand-green);color:var(--white);padding:0 8px;margin-right:20px}
.hero-text{position:absolute;left:208px;top:206px;font-size:19px;font-weight:900;font-style:italic;color:#3a4048;line-height:28px}
.hero-cta{position:absolute;left:205px;top:293px;width:208px;height:33px;background:var(--white);display:flex;align-items:center;font-size:17px;font-weight:900;font-style:italic;color:#1a1a1a}
.hero-cta .cta-arrow{width:33px;height:33px;background:var(--brand-green);display:flex;align-items:center;justify-content:center;margin-right:10px}
.slide-arrow{position:absolute;top:262px;width:38px;height:38px;border-radius:50%;background:#f2f2f2;border:2px solid #bcbcbc;display:flex;align-items:center;justify-content:center}
.slide-arrow--prev{left:120px}
.slide-arrow--next{left:1038px}
.service-band{position:absolute;left:139px;top:476px;width:923px;height:88px;background:var(--brand-blue);background-image:repeating-linear-gradient(0deg,rgba(255,255,255,.05) 0 1px,transparent 1px 3px)}
.service{position:absolute;top:436px;width:110px;text-align:center;color:var(--white);font-size:15px}
.service-circle{width:90px;height:90px;margin:0 auto 6px;border-radius:50%;background:radial-gradient(circle at 50% 35%,#8a8a8a,var(--circle-grey));border:4px solid #4b4b4b;display:flex;align-items:center;justify-content:center}
.service.is-active .service-circle{background:radial-gradient(circle at 50% 35%,#86d03b,#52a017);border-color:#3f7c12}
.content{position:absolute;left:139px;top:564px;width:923px;height:248px;background:var(--white)}
.welcome{position:absolute;left:154px;top:606px;width:600px}
.section-title{font-size:18px;color:#222;font-weight:400}
.section-title span{color:var(--brand-blue)}
.rule{position:relative;height:2px;margin-top:8px;border-top:1px dashed #7a8ea3}
.rule::before{content:"";position:absolute;left:0;top:-2px;width:110px;height:2px;background:var(--brand-blue)}
.rule::after{content:"";position:absolute;left:108px;top:-5px;width:8px;height:8px;border-radius:50%;background:var(--ink)}
.welcome p{margin-top:18px;padding-left:6px;font-family:'Open Sans',sans-serif;font-size:12.4px;line-height:23.5px;color:#333}
.welcome p b{font-size:11px;color:#111}
.divider{position:absolute;left:771px;top:594px;width:2px;height:206px;background:#e3e3e3}
.what-we-do{position:absolute;left:794px;top:598px;width:248px}
.what-we-do .section-title{font-size:19px;font-weight:700;color:var(--ink)}
.what-we-do .rule::before{width:110px}
.feature{display:flex;gap:12px;margin-top:18px}
.feature:first-of-type{margin-top:14px}
.feature h3{font-size:16px;font-weight:700;color:var(--brand-blue)}
.feature p{font-family:'Open Sans',sans-serif;font-size:12.4px;color:#444;line-height:15px}
.clients{position:absolute;left:139px;top:812px;width:923px;height:98px;background:var(--grey-band)}
.clients-tab{position:absolute;left:552px;top:812px;width:120px;height:26px;background:#5b5b5b;color:var(--white);font-size:18px;text-align:center;line-height:26px;clip-path:polygon(8% 0,92% 0,100% 100%,0 100%)}
.client-list{position:absolute;left:290px;top:856px;display:flex;gap:40px;font-size:21px;font-weight:700;color:#8a8a8a}
.client{display:flex;align-items:center;gap:6px}
.client i{width:12px;height:12px;border-radius:50%;background:#9a9a9a;display:block}
.footer-nav{position:absolute;left:140px;top:929px;font-size:12.5px;font-weight:700;color:var(--white);display:flex;gap:10px}
.footer-nav span{color:#bbb}
.footer-contact{position:absolute;top:927px;font-size:12.5px;color:var(--white);line-height:20px;display:flex;gap:8px}
.footer-address{left:436px}
.footer-phone{left:612px;flex-direction:column;gap:0}
.footer-phone div{display:flex;align-items:center;gap:8px}
.subscribe{position:absolute;left:802px;top:928px;display:flex;height:32px}
.subscribe-input{width:170px;background:var(--white);display:flex;align-items:center;gap:8px;padding-left:10px;font-size:12px;font-style:italic;color:#999}
.subscribe-btn{width:90px;background:var(--brand-blue);color:var(--white);font-size:13px;font-weight:700;display:flex;align-items:center;justify-content:center}
.bottom-bar{position:absolute;left:0;top:974px;width:1200px;height:28px;background:var(--brand-blue)}
.copyright{position:absolute;left:140px;top:981px;font-size:12px;color:var(--white)}
.social{position:absolute;left:948px;top:978px;display:flex;gap:8px}
.social i{width:21px;height:21px;border-radius:50%;border:1.5px solid var(--white);display:block}
</style>
</head>
<body>
<div class="side-art side-art--left" role="img" aria-label="Glowing globe of travel photos"></div>
<div class="side-art side-art--right" role="img" aria-label="Glowing globe of travel photos"></div>

<div class="hero" role="img" aria-label="Businessman sketching an airplane and world landmarks on a glass board"></div>

<div class="phone-top">
  <span class="icon-dot"><svg width="16" height="16" viewBox="0 0 24 24"><path fill="#fff" d="M6.6 10.8a15 15 0 0 0 6.6 6.6l2.2-2.2c.3-.3.7-.4 1-.2 1.1.4 2.3.6 3.6.6.6 0 1 .4 1 1V20c0 .6-.4 1-1 1A17 17 0 0 1 3 4c0-.6.4-1 1-1h3.5c.6 0 1 .4 1 1 0 1.3.2 2.5.6 3.6.1.3 0 .7-.2 1z"/></svg></span>
  123-456-7890
</div>

<svg class="header-bar" viewBox="0 0 966 67" preserveAspectRatio="none"><polygon points="0,0 912,0 966,33.5 912,67 0,67" fill="#fff"/></svg>

<div class="brand">
  <span class="brand-mark"></span>
  <div>
    <div class="brand-name">BRIVANE</div>
    <div class="brand-sub">STRATEGY MANAGEMENT, INC.</div>
  </div>
</div>

<nav class="nav">
  <a class="is-active" href="#">Home</a>
  <a href="#">About Us</a>
  <a href="#">Our Services</a>
  <a href="#">Contact Us</a>
</nav>

<div class="hero-text">Lorem ipsum dolor sit amet,<br>consectetuer adipisemy nibh<br>euismod tincidunt</div>
<div class="hero-cta"><span class="cta-arrow"><svg width="12" height="16" viewBox="0 0 12 16"><path d="M2 1l8 7-8 7" stroke="#fff" stroke-width="3" fill="none"/></svg></span>Get Started With Us !</div>

<div class="slide-arrow slide-arrow--prev"><svg width="12" height="16" viewBox="0 0 12 16"><path d="M9 2L3 8l6 6" stroke="#333" stroke-width="3" fill="none"/></svg></div>
<div class="slide-arrow slide-arrow--next"><svg width="12" height="16" viewBox="0 0 12 16"><path d="M3 2l6 6-6 6" stroke="#333" stroke-width="3" fill="none"/></svg></div>

<div class="service-band"></div>

<div class="service is-active" style="left:339px">
  <div class="service-circle"><svg width="36" height="36" viewBox="0 0 36 36"><rect x="5" y="5" width="22" height="26" fill="none" stroke="#fff" stroke-width="3"/><path d="M12 24l16-16 3 3-16 16h-3z" fill="#fff"/></svg></div>Planning
</div>
<div class="service" style="left:454px">
  <div class="service-circle"><svg width="36" height="36" viewBox="0 0 36 36"><path d="M7 29L27 9M7 7l22 22" stroke="#fff" stroke-width="4" stroke-linecap="round"/><circle cx="27" cy="8" r="5" fill="none" stroke="#fff" stroke-width="3"/></svg></div>Development
</div>
<div class="service" style="left:570px">
  <div class="service-circle"><svg width="36" height="36" viewBox="0 0 36 36"><rect x="6" y="18" width="5" height="12" fill="#fff"/><rect x="13" y="10" width="5" height="20" fill="#fff"/><rect x="20" y="14" width="5" height="16" fill="#fff"/><rect x="27" y="20" width="4" height="10" fill="#fff"/><rect x="4" y="31" width="29" height="2" fill="#fff"/></svg></div>Analysis
</div>
<div class="service" style="left:689px">
  <div class="service-circle"><svg width="36" height="36" viewBox="0 0 36 36"><circle cx="18" cy="18" r="13" fill="none" stroke="#fff" stroke-width="2.5"/><ellipse cx="18" cy="18" rx="6" ry="13" fill="none" stroke="#fff" stroke-width="2"/><path d="M5 18h26M8 11h20M8 25h20" stroke="#fff" stroke-width="2"/></svg></div>Marketing
</div>
<div class="service" style="left:804px">
  <div class="service-circle"><svg width="36" height="36" viewBox="0 0 36 36"><circle cx="17" cy="19" r="13" fill="none" stroke="#fff" stroke-width="3"/><circle cx="17" cy="19" r="7" fill="none" stroke="#fff" stroke-width="3"/><circle cx="17" cy="19" r="2" fill="#fff"/><path d="M17 19L31 5" stroke="#fff" stroke-width="3"/></svg></div>Solutions
</div>

<div class="content"></div>

<section class="welcome">
  <h2 class="section-title">Welcome to <span>Brivane Strategy Management, Inc.</span></h2>
  <div class="rule"></div>
  <p>Lorem ipsum dolor sit amet, consectetu adipiscing elit, sed diam nonummy nibh euismod tincidunt ut laoreet dolore magna aliquam erat volutpat.  wisi enim ad minim veniam, quisLorem ipsum dolor sit amet, consectetu adipiscing elit, sed diam Lorem ipsum dolor sit amet, consectetu adipiscing elit, sed diam nonummy nibh euismod tincidunt ut laoreet dolore magna aliquam erat volutpat.  wisi enim ad minim veniam, quisLorem ipsum dolor sit amet, consectetu adipiscing elit, sed diam ...<b>Read more</b></p>
</section>

<div class="divider"></div>

<section class="what-we-do">
  <h2 class="section-title">What We <span>Do</span></h2>
  <div class="rule"></div>
  <div class="feature">
    <svg width="26" height="26" viewBox="0 0 26 26"><circle cx="13" cy="7" r="4" fill="#555"/><path d="M5 20c2-6 14-6 16 0z" fill="#555"/><path d="M1 20h24" stroke="#555" stroke-width="2"/></svg>
    <div><h3>Our Experties</h3><p>Ut wisi enim ad minim venia m, quisip nostrud exerci tation ullamcor.</p></div>
  </div>
  <div class="feature">
    <svg width="26" height="26" viewBox="0 0 26 26"><circle cx="13" cy="13" r="4" fill="#555"/><g fill="#555"><circle cx="13" cy="3" r="2"/><circle cx="13" cy="23" r="2"/><circle cx="3" cy="13" r="2"/><circle cx="23" cy="13" r="2"/><circle cx="6" cy="6" r="2"/><circle cx="20" cy="20" r="2"/><circle cx="20" cy="6" r="2"/><circle cx="6" cy="20" r="2"/></g></svg>
    <div><h3>Our Management</h3><p>Ut wisi enim ad minim venia m, quisip nostrud exerci tation ullamcor.</p></div>
  </div>
</section>

<div class="clients"></div>
<div class="clients-tab">Our Clients</div>
<div class="client-list">
  <span class="client"><i></i>Veltrix</span>
  <span class="client">Norpa</span>
  <span class="client">Kestel</span>
  <span class="client">Ridgeway</span>
  <span class="client">Solvane</span>
</div>

<div class="footer-nav">Home <span>|</span> About Us <span>|</span> Services <span>|</span> Contact Us</div>

<div class="footer-contact footer-address">
  <svg width="12" height="16" viewBox="0 0 12 16" style="margin-top:3px"><path d="M6 0a6 6 0 0 1 6 6c0 4-6 10-6 10S0 10 0 6a6 6 0 0 1 6-6z" fill="#fff"/><circle cx="6" cy="6" r="2" fill="#1d1a18"/></svg>
  <div>Lorem ipsum dolor sit amet,<br>consectetuer adimpisciged</div>
</div>

<div class="footer-contact footer-phone">
  <div><svg width="12" height="12" viewBox="0 0 24 24"><path fill="#fff" d="M6.6 10.8a15 15 0 0 0 6.6 6.6l2.2-2.2c.3-.3.7-.4 1-.2 1.1.4 2.3.6 3.6.6.6 0 1 .4 1 1V20c0 .6-.4 1-1 1A17 17 0 0 1 3 4c0-.6.4-1 1-1h3.5c.6 0 1 .4 1 1 0 1.3.2 2.5.6 3.6.1.3 0 .7-.2 1z"/></svg>123-456-7890</div>
  <div><svg width="12" height="10" viewBox="0 0 12 10"><rect width="12" height="10" fill="#fff"/><path d="M0 0l6 5 6-5" stroke="#1d1a18" fill="none"/></svg>info@brivanestrategy.com</div>
</div>

<div class="subscribe">
  <div class="subscribe-input"><svg width="14" height="11" viewBox="0 0 12 10"><rect width="12" height="10" fill="#ccc"/><path d="M0 0l6 5 6-5" stroke="#fff" fill="none"/></svg>your e-mail address</div>
  <div class="subscribe-btn">SUBSCRIBE</div>
</div>

<div class="bottom-bar"></div>
<div class="copyright">Copyright © 2014  Brivane Strategy.All Right Reserved</div>
<div class="social" aria-label="Social links"><i></i><i></i><i></i><i></i></div>
</body>
</html>
```